Create a proposal + product powerpoint

Please see the powerpoint for the slides. There are about 20 slides to be created. Rest of them are for reference and show the design that I like.

I would like to move fast on this, since I need to present it next week (in the week of April 21st).

Please download the current content from here:
https://www.parcelbrook.net/fetch/qRtVmXzLwPkNbYcD

Please make at least 4 slides with the specific content so I can assess your design style.

Target Market(s)

Business Audience and very senior technical audience
Decision Makers

Industry/Entity Type

Product

Colors
e34297
a64599

Requirements
Must have
• Should be very clean, crisp.

I like to use Icons as shown in the powerpoint.... Please see the appendix of the slide deck that shows the various icons. Most of them just have plain text, and I would like to organize so that it does not look like some is just reading text.

I would like to focus on the design aspects so that the audience is clear on how the solution works.

Every page should some graphic element based on the slides shown in the appendix.

```html
<!DOCTYPE html>
<html lang="en">
<head>
<meta charset="utf-8">
<title>Lifecycle management solution</title>
<link href="https://fonts.googleapis.com/css2?family=Roboto+Condensed:wght@400;500&display=swap" rel="stylesheet">
<style>
  :root {
    --title: #93178f;
    --tile: #c545b5;
    --tile-border: #ffffff;
    --rule: #d4d4d4;
    --footer-dark: #9a1f5d;
    --footer-light: #a64599;
    --logo-text: #9a9a9a;
    --white: #ffffff;
  }
  * { margin: 0; padding: 0; box-sizing: border-box; }
  html, body { width: 1200px; height: 900px; overflow: hidden; background: var(--white); }
  .slide {
    position: relative;
    width: 1200px;
    height: 900px;
    overflow: hidden;
    background: var(--white);
    font-family: "Roboto Condensed", "Arial Narrow", sans-serif;
  }
  .backdrop-glow {
    position: absolute;
    left: -200px;
    top: 420px;
    width: 700px;
    height: 360px;
    background: radial-gradient(ellipse at 20% 45%, rgba(197, 69, 181, 0.32), rgba(197, 69, 181, 0) 65%);
  }
  .backdrop-mosaic {
    position: absolute;
    right: 0;
    top: 92px;
    width: 340px;
    height: 750px;
    background:
      linear-gradient(120deg, rgba(255,255,255,1) 0%, rgba(255,255,255,0) 45%),
      linear-gradient(180deg, rgba(205, 110, 215, 0.55) 0%, rgba(200, 80, 210, 0.8) 45%, rgba(225, 170, 235, 0.6) 100%);
    clip-path: polygon(35% 0, 100% 0, 100% 100%, 0 100%, 30% 55%, 10% 30%);
  }
  .header-title {
    position: absolute;
    left: 40px;
    top: 14px;
    font-size: 54px;
    font-weight: 400;
    color: var(--title);
    letter-spacing: -0.5px;
  }
  .header-rule {
    position: absolute;
    left: 40px;
    top: 90px;
    width: 1160px;
    height: 2px;
    background: var(--rule);
  }
  .logo-box {
    position: absolute;
    left: 1035px;
    top: 12px;
    width: 150px;
    height: 68px;
    border-radius: 8px;
    background: var(--white);
    box-shadow: 0 0 6px rgba(0,0,0,0.18);
    display: flex;
    align-items: center;
    justify-content: center;
    font-size: 28px;
    color: var(--logo-text);
  }
  .feature-row {
    position: absolute;
    left: 40px;
    top: 196px;
    display: flex;
    gap: 5px;
  }
  .feature-tile {
    width: 211px;
    height: 268px;
    background: var(--tile);
    border: 2px solid var(--tile-border);
    color: var(--white);
    text-align: center;
  }
  .feature-icon {
    display: block;
    margin: 40px auto 0;
    width: 80px;
    height: 80px;
  }
  .feature-label {
    margin-top: 28px;
    font-size: 35px;
    line-height: 1.15;
    font-weight: 400;
  }
  .feature-label.small { font-size: 31px; }
  .footer {
    position: absolute;
    left: 0;
    bottom: 0;
    width: 1200px;
    height: 58px;
  }
  .footer svg { position: absolute; left: 0; top: 0; }
  .footer-page, .footer-copy {
    position: absolute;
    top: 0;
    line-height: 58px;
    font-size: 24px;
    color: var(--white);
    letter-spacing: 0.5px;
  }
  .footer-page { left: 15px; }
  .footer-copy { right: 15px; }
</style>
</head>
<body>
<main class="slide">
  <div class="backdrop-glow" role="img" aria-label="Soft purple glow"></div>
  <div class="backdrop-mosaic" role="img" aria-label="Purple geometric triangle backdrop"></div>

  <h1 class="header-title">Lifecycle management solution</h1>
  <div class="header-rule"></div>
  <div class="logo-box">LOGO HERE</div>

  <section class="feature-row">
    <article class="feature-tile">
      <svg class="feature-icon" viewBox="0 0 80 80" fill="none" stroke="#fff" stroke-width="7" stroke-linecap="square">
        <polyline points="24,22 8,40 24,58"/>
        <polyline points="56,22 72,40 56,58"/>
        <line x1="46" y1="30" x2="34" y2="50"/>
      </svg>
      <h2 class="feature-label">Code<br>Promotion</h2>
    </article>
    <article class="feature-tile">
      <svg class="feature-icon" viewBox="0 0 80 80" fill="#fff">
        <circle cx="40" cy="16" r="5"/>
        <rect x="35" y="23" width="10" height="20" rx="2"/>
        <circle cx="22" cy="24" r="4"/>
        <rect x="18" y="30" width="8" height="15" rx="2"/>
        <circle cx="58" cy="24" r="4"/>
        <rect x="54" y="30" width="8" height="15" rx="2"/>
        <path d="M20 52 Q40 44 60 52 L54 58 Q40 54 34 60 L44 72 L30 72 L24 60 Z"/>
      </svg>
      <h2 class="feature-label">Change<br>Management</h2>
    </article>
    <article class="feature-tile">
      <svg class="feature-icon" viewBox="0 0 80 80" fill="none" stroke="#fff" stroke-width="8" stroke-linecap="round">
        <line x1="14" y1="14" x2="66" y2="66"/>
        <line x1="60" y1="18" x2="18" y2="62"/>
        <circle cx="62" cy="16" r="8" stroke-width="5"/>
      </svg>
      <h2 class="feature-label">Trouble<br>Shooting</h2>
    </article>
    <article class="feature-tile">
      <svg class="feature-icon" viewBox="0 0 80 80" fill="none" stroke="#fff" stroke-width="4" stroke-dasharray="4 3">
        <circle cx="28" cy="18" r="8"/>
        <circle cx="54" cy="44" r="13"/>
        <circle cx="22" cy="52" r="10"/>
        <circle cx="54" cy="44" r="4" stroke-dasharray="none"/>
      </svg>
      <h2 class="feature-label small">Build and<br>test automation</h2>
    </article>
    <article class="feature-tile">
      <svg class="feature-icon" viewBox="0 0 80 80" fill="none" stroke="#fff" stroke-width="6" stroke-linecap="round">
        <circle cx="34" cy="32" r="20"/>
        <line x1="50" y1="48" x2="66" y2="64" stroke-width="9"/>
        <circle cx="34" cy="27" r="5" fill="#fff" stroke="none"/>
        <path d="M24 42 Q34 30 44 42 Z" fill="#fff" stroke="none"/>
      </svg>
      <h2 class="feature-label">Audit<br>Analysis</h2>
    </article>
  </section>

  <footer class="footer">
    <svg width="1200" height="58" viewBox="0 0 1200 58">
      <polygon points="0,0 906,0 940,58 0,58" fill="var(--footer-dark)"/>
      <polygon points="918,0 1200,0 1200,58 952,58" fill="var(--footer-light)"/>
    </svg>
    <span class="footer-page">Page : 01</span>
    <span class="footer-copy">Copyright text here</span>
  </footer>
</main>
</body>
</html>
```